International Business Development Firm, in need of Branded Stationery material

We just made our Logo and now we are looking for branded stationery for our company such as:

* A Letterhead with our company's name, address, and logo at the top in Word format for easy editing
* A more formal letter format with a light background design (watermark) featuring our logo, allowing us to write over it for various documents and presentations
* Business card + Envelopes are a plus but not a must
* PowerPoint for company and product introductions
* An Info sheet with Bullet Points

The design should be professional.
Please ensure the design is high quality and print ready.

Target Market(s)

Businesses and high net value individuels

Industry/Entity Type

International Business Development Firm

Colors

Designer to choose colors to be used in the design.

Requirements
Must have
• word docs so i can use the stationery templates afterwards

```html
<!DOCTYPE html>
<html lang="en">
<head>
<meta charset="utf-8">
<title>Veloria Partners – Envelope</title>
<link rel="stylesheet" href="https://fonts.googleapis.com/css2?family=PT+Sans+Narrow:wght@700&family=PT+Sans:wght@400&display=swap">
<style>
  :root {
    --paper: #ffffff;
    --panel: #ddebf1;
    --header-purple: #8466a3;
    --band-purple: #744b93;
    --ink-purple: #6a4b8c;
    --title-ink: #ddebf1;
  }
  html, body {
    margin: 0;
    padding: 0;
    width: 1200px;
    height: 603px;
    overflow: hidden;
    background: var(--paper);
  }
  .envelope {
    position: relative;
    width: 1200px;
    height: 603px;
    background: var(--paper);
  }
  .envelope-panel {
    position: absolute;
    left: 29px;
    top: 34px;
    width: 1143px;
    height: 545px;
    background: var(--panel);
  }
  .header-band {
    position: absolute;
    left: 0;
    top: 0;
    width: 797px;
    height: 116px;
    background: var(--header-purple);
  }
  .header-title {
    position: absolute;
    left: 20px;
    top: 18px;
    width: 760px;
    height: 90px;
    overflow: visible;
  }
  .header-title text {
    font-family: "PT Sans Narrow", "Arial Narrow", sans-serif;
    font-weight: 700;
    font-size: 90px;
    fill: var(--title-ink);
  }
  .brand {
    position: absolute;
    left: 830px;
    top: 44px;
    display: flex;
    align-items: center;
    gap: 14px;
    font-family: "PT Sans Narrow", "Arial Narrow", sans-serif;
    font-weight: 700;
    font-size: 40px;
    letter-spacing: 1px;
    color: var(--ink-purple);
    text-transform: uppercase;
  }
  .brand-mark {
    width: 26px;
    height: 26px;
    background: var(--ink-purple);
  }
  .contact-line {
    position: absolute;
    left: 20px;
    top: 478px;
    width: 1105px;
    height: 30px;
    overflow: visible;
  }
  .contact-line text {
    font-family: "PT Sans", "Myriad Pro", sans-serif;
    font-size: 24px;
    fill: var(--ink-purple);
  }
  .footer-band {
    position: absolute;
    left: 0;
    bottom: 0;
    width: 1143px;
    height: 40px;
    background: var(--band-purple);
  }
</style>
</head>
<body>
  <div class="envelope">
    <div class="envelope-panel">
      <div class="header-band">
        <svg class="header-title" viewBox="0 0 760 90" aria-label="International Business Development Firm">
          <text x="0" y="80" textLength="757" lengthAdjust="spacingAndGlyphs">International Business Development Firm</text>
        </svg>
      </div>

      <div class="brand">
        <span class="brand-mark"></span>
        <span class="brand-name">Veloria Partners</span>
      </div>

      <svg class="contact-line" viewBox="0 0 1105 30">
        <text x="0" y="24" textLength="1103" lengthAdjust="spacingAndGlyphs">Address: aaaaaaaa, bbbbbbbb, cccccccccccc-Phone: 00000000000, Email: veloriapartners.com, Web: www.veloria.com</text>
      </svg>

      <div class="footer-band"></div>
    </div>
  </div>
</body>
</html>
```